New Stationary and Logo Design for Start Up Company

We need a logo design and stationary set including letterhead, business card (double sided), compliments slip and envelope for a new company Bright Harbour Media.
The files should be editable to update address and standard contact details, will need to forward to web designer and stationary printer.
The company will be an online marketer and distributer of various business education products in Australia.
The designs should convey simple clean image
Target Market(s)
Small business owners and professional service providers (ie Accountants, Lawyers, Real Estate Agents) in Australia
Industry/Entity Type
Education
Look and feel
Each slider illustrates characteristics of the customer's brand and the style your logo design should communicate.

```html
<!DOCTYPE html>
<html lang="en">
<head>
<meta charset="utf-8">
<title>Bright Harbour Media – Compliments Slip</title>
<link rel="stylesheet" href="https://fonts.googleapis.com/css2?family=Arimo:wght@400;700&display=swap">
<style>
  :root {
    --page-bg: #f4f5f6;
    --paper: #ffffff;
    --brand-blue: #1a9ad6;
    --ink: #4a4f56;
    --ink-strong: #3f444b;
    --signature-tone: #d9dadc;
  }
  * { box-sizing: border-box; margin: 0; padding: 0; }
  html, body {
    width: 1200px;
    height: 608px;
    overflow: hidden;
    background: var(--page-bg);
    font-family: "Arimo", Arial, sans-serif;
    color: var(--ink);
  }
  .slip {
    position: absolute;
    left: 36px;
    top: 38px;
    width: 1130px;
    height: 534px;
    background: var(--paper);
  }
  .brand-name {
    position: absolute;
    left: 36px;
    top: 42px;
    font-size: 31px;
    font-weight: 400;
    letter-spacing: -0.6px;
    color: var(--brand-blue);
    line-height: 1;
  }
  .message {
    position: absolute;
    left: 249px;
    top: 196px;
    width: 610px;
    font-size: 12.6px;
    line-height: 17.2px;
    color: var(--ink);
  }
  .signature {
    position: absolute;
    left: 636px;
    top: 262px;
    width: 198px;
    height: 74px;
  }
  .contact {
    position: absolute;
    left: 882px;
    top: 437px;
    height: 71px;
    padding-left: 23px;
    border-left: 0;
  }
  .contact-bracket {
    position: absolute;
    left: 0;
    top: 0;
    width: 15px;
    height: 71px;
  }
  .contact-list {
    list-style: none;
    font-size: 12.6px;
    line-height: 15.6px;
    padding-top: 3px;
    color: var(--ink);
  }
  .contact-label {
    font-weight: 700;
    color: var(--ink-strong);
  }
</style>
</head>
<body>
  <main class="slip">
    <div class="brand-name">Bright Harbour Media</div>

    <p class="message">
      Lorem ipsum dolor sit amet, consectetur adipiscing elit. Aenean orci metus, consequat quis
      hendrerit ac, euismod a dolor. Duis eget rutrum velit. Aenean congue purus urna, vitae rhoncus nibh.
      Pellentesque condimentum sollicitudin justo id tempor. Donec malesuada eros eu mi pharetra
      adipiscing. Donec feugiat nisl vitae dolor dignissim dapibus. Proin.
    </p>

    <svg class="signature" role="img" aria-label="Handwritten signature" viewBox="0 0 198 74">
      <defs>
        <linearGradient id="signature-fill" x1="0" x2="1" y1="0" y2="0">
          <stop offset="0" stop-color="var(--signature-tone)"/>
          <stop offset="1" stop-color="var(--signature-tone)" stop-opacity="0.25"/>
        </linearGradient>
      </defs>
      <rect width="198" height="74" fill="url(#signature-fill)"/>
    </svg>

    <address class="contact" style="font-style:normal">
      <svg class="contact-bracket" viewBox="0 0 15 71" aria-hidden="true">
        <path d="M14 1.5H2.5V69.5H14" fill="none" stroke="var(--brand-blue)" stroke-width="3.5"/>
      </svg>
      <ul class="contact-list">
        <li><span class="contact-label">adress:</span> 218 Wharf Lane</li>
        <li><span class="contact-label">tel:</span> 02.7310.4418</li>
        <li><span class="contact-label">e-mail:</span> info@brightharbour.com.au</li>
        <li><span class="contact-label">web:</span> www.brightharbour.com.au</li>
      </ul>
    </address>
  </main>
</body>
</html>
```